Refresh of graphic design for existing website

We would like to refresh our website. Please see the attached design specifications.

Industry/Entity Type

Graphic Design

```html
<!DOCTYPE html>
<html lang="en">
<head>
<meta charset="utf-8">
<title>Vantor Tool Council</title>
<link href="https://fonts.googleapis.com/css2?family=Open+Sans:wght@400;600;700&display=swap" rel="stylesheet">
<style>
:root{
  --green:#17a673;
  --green-dark:#128a5f;
  --blue:#0d5fae;
  --blue-dark:#0a4a8c;
  --navy:#083e78;
  --ink:#333a40;
  --muted:#7a8188;
  --line:#e2e5e8;
  --page:#ffffff;
  --bg:#f1f2f4;
}
*{box-sizing:border-box;margin:0;padding:0}
html,body{width:756px;height:1200px;overflow:hidden;background:var(--bg)}
body{font-family:"Open Sans",Arial,sans-serif;color:var(--ink);font-size:7px;line-height:1.5}
.site{position:relative;width:756px;height:1200px;background:var(--page);margin:0 auto;overflow:hidden}
.abs{position:absolute}

/* header */
.brand{left:30px;top:12px;display:flex;align-items:center;gap:8px}
.brand-dot{width:34px;height:34px;border-radius:50%;background:var(--blue)}
.brand-name{font-size:17px;font-weight:700;color:var(--blue);line-height:1}
.brand-sub{font-size:8px;color:var(--blue);font-weight:600;margin-top:3px}
.search{right:30px;top:22px;display:flex;gap:4px}
.search span{display:block;height:14px;border:1px solid var(--line);font-size:6px;color:var(--muted);padding:2px 5px;width:70px}
.search b{display:block;height:14px;background:var(--green);color:#fff;font-size:6px;padding:2px 8px}

.nav{left:30px;right:30px;top:76px;height:20px;background:var(--blue);display:flex}
.nav a{color:#fff;font-size:6.5px;font-weight:600;text-decoration:none;padding:0 12px;line-height:20px}
.nav a.active{background:var(--green)}

/* hero */
.hero{left:0;right:0;top:96px;height:352px;background:linear-gradient(135deg,#4c5560 0%,#2c333b 40%,#6b6f72 70%,#3a4048 100%)}
.hero-arrow{top:262px;width:16px;height:24px}
.hero-band{left:0;top:362px;width:470px;height:68px;background:var(--green)}
.hero-band svg{position:absolute;right:-40px;top:0}
.hero-title{left:40px;top:372px;color:#fff;font-size:18px;font-weight:700}
.hero-sub{left:40px;top:398px;color:#fff;font-size:8px;width:240px;line-height:1.35}

/* sections */
.h2{font-size:9.5px;font-weight:700;color:var(--ink);text-transform:uppercase}
.rule{height:1px;background:var(--line)}
.btn{display:inline-block;background:var(--green);color:#fff;font-size:5.5px;font-weight:700;padding:3px 8px;text-transform:uppercase}
.btn.line{background:none;border:1px solid var(--muted);color:var(--ink)}
.photo{background:linear-gradient(135deg,#8b949c,#3f4a55)}
p.txt{font-size:6px;color:var(--muted);line-height:1.6}

.welcome-img{left:35px;top:490px;width:110px;height:80px}
.welcome-text{left:160px;top:488px;width:560px}
.welcome-text p{margin-bottom:8px}
.welcome-text .lead{color:var(--ink)}

.event{top:692px;width:118px}
.event .photo{height:56px}
.event .date{font-size:6px;color:var(--green);font-weight:600;margin:6px 0 3px}
.event p{margin-bottom:10px}

.member{left:428px;top:655px;width:290px;height:110px;background:linear-gradient(180deg,#f3f5f7,#e5e9ed)}
.join{left:650px;top:725px;background:var(--blue);color:#fff;font-size:7px;font-weight:700;padding:4px 10px}
.member-text{left:428px;top:775px;width:290px}
.member-text h3{font-size:6.5px;font-weight:700;color:var(--blue);margin-bottom:3px}
.member-text em{color:var(--green);font-style:normal}

.news{display:flex;gap:8px;width:220px}
.datebox{flex:0 0 34px;height:38px;background:var(--green);color:#fff;text-align:center;line-height:1.1;padding-top:5px}
.datebox small{display:block;font-size:6px;font-weight:600}
.datebox strong{display:block;font-size:13px}
.news p{color:var(--ink)}

/* footer */
.footer{left:0;right:0;top:1030px;height:170px;background:var(--blue-dark)}
.fcol{top:1040px;color:#cfe0f2}
.fcol h4{font-size:7px;font-weight:700;color:#fff;text-transform:uppercase;margin-bottom:6px}
.fcol p,.fcol li{font-size:5.8px;line-height:1.7;list-style:none}
.subscribe{display:flex;margin-top:8px}
.subscribe span{background:#fff;color:var(--muted);font-size:5.5px;padding:3px 6px;width:110px}
.subscribe b{background:var(--green);color:#fff;font-size:5.5px;padding:3px 8px}
.contact-row{display:flex;gap:5px;align-items:flex-start;margin-bottom:3px}
.social li{display:flex;align-items:center;gap:6px;margin-bottom:5px}
.social i{width:13px;height:13px;border-radius:50%;background:var(--blue);border:1px solid #5f93c9;display:block}
.copy{left:0;right:0;top:1180px;height:20px;background:var(--navy);color:#9fbad6;font-size:5.5px;text-align:center;line-height:20px}
</style>
</head>
<body>
<div class="site">

  <header>
    <div class="abs brand">
      <span class="brand-dot"></span>
      <div><div class="brand-name">VTC</div><div class="brand-sub">Vantor Tool Council</div></div>
    </div>
    <div class="abs search"><span>Username</span><span>Password</span><b>LOGIN</b></div>
    <nav class="abs nav">
      <a class="active">HOME</a><a>ABOUT VTC</a><a>NEWS</a><a>MEMBERSHIP</a><a>EVENTS</a><a>MEMBERS ONLY</a><a>CONTACT US</a>
    </nav>
  </header>

  <section>
    <div class="abs hero" role="img" aria-label="Photo of technicians working on a car engine with wrenches"></div>
    <svg class="abs hero-arrow" style="left:8px" viewBox="0 0 16 24"><path d="M12 2 3 12l9 10" fill="none" stroke="#fff" stroke-width="2.5"/></svg>
    <svg class="abs hero-arrow" style="right:8px" viewBox="0 0 16 24"><path d="M4 2l9 10-9 10" fill="none" stroke="#fff" stroke-width="2.5"/></svg>
    <div class="abs hero-band"><svg width="40" height="68" viewBox="0 0 40 68"><path d="M0 0h40L0 68z" fill="#17a673"/></svg></div>
    <div class="abs hero-title">Vantor Tool Council</div>
    <div class="abs hero-sub">Lorem ipsum dolor sit amet, consectetur adipis ing elit, sed do eiusmod tempor incididunt.</div>
  </section>

  <section>
    <div class="abs h2" style="left:35px;top:464px">Welcome to Vantor Tool Council</div>
    <div class="abs rule" style="left:35px;right:35px;top:480px"></div>
    <div class="abs photo welcome-img" role="img" aria-label="Photo of a mechanic servicing a car in a workshop"></div>
    <div class="abs welcome-text">
      <p class="txt lead">VTC's mission is to advance the vehicle service industry by providing technical data and open dialog between the makers of transportation products, government regulators and the providers of tools, equipment and service information.</p>
      <p class="txt">VTC is one of the most respected associations in the automotive aftermarket, joining tool, equipment and software makers with service providers to share data and shape training across the whole industry.</p>
      <span class="btn">Read more</span>
    </div>
  </section>

  <section>
    <div class="abs h2" style="left:35px;top:668px">Upcoming Events</div>
    <div class="abs rule" style="left:35px;width:368px;top:684px"></div>
    <article class="abs event" style="left:35px"><div class="photo" role="img" aria-label="Photo of an engine bay"></div><div class="date">Aug 27, 2015</div><p class="txt">Lorem ipsum dolor sit amet, consectetur adipiscing elit, sed do eiusmod tempor incididunt ut labore.</p><span class="btn line">Read more</span></article>
    <article class="abs event" style="left:160px"><div class="photo" role="img" aria-label="Photo of a technician at a vehicle"></div><div class="date">Aug 27, 2015</div><p class="txt">Lorem ipsum dolor sit amet, consectetur adipiscing elit, sed do eiusmod tempor incididunt ut labore.</p><span class="btn line">Read more</span></article>
    <article class="abs event" style="left:285px"><div class="photo" role="img" aria-label="Photo of a diagnostic tool in use"></div><div class="date">Aug 27, 2015</div><p class="txt">Lorem ipsum dolor sit amet, consectetur adipiscing elit, sed do eiusmod tempor incididunt ut labore.</p><span class="btn line">Read more</span></article>

    <div class="abs member" role="img" aria-label="Illustration of a smiling mechanic holding a wrench"></div>
    <div class="abs join">JOIN VTC</div>
    <div class="abs member-text">
      <h3>MEMBERSHIP BENEFITS</h3>
      <p class="txt">Lorem ipsum dolor sit amet, consectetur <em>adipiscing elit sed do eiusmod tempor</em> ut labore et dolore magna aliqua enim.</p>
      <p class="txt">Ut enim ad minim veniam, <em>quis nostrud exercitation ullamco</em> laboris nisi aliquip ex ea commodo.</p>
    </div>
  </section>

  <section>
    <div class="abs h2" style="left:35px;top:902px">Industry News</div>
    <div class="abs rule" style="left:35px;right:35px;top:918px"></div>
    <div class="abs news" style="left:35px;top:932px"><div class="datebox"><small>OCT</small><strong>18</strong></div><p class="txt">Lorem ipsum dolor sit amet, consectetur adipiscing elit, sed do eiusmod tempor incididunt labore.</p></div>
    <div class="abs news" style="left:270px;top:932px"><div class="datebox"><small>OCT</small><strong>18</strong></div><p class="txt">Lorem ipsum dolor sit amet, consectetur adipiscing elit, sed do eiusmod tempor incididunt labore.</p></div>
    <div class="abs news" style="left:505px;top:932px"><div class="datebox"><small>OCT</small><strong>18</strong></div><p class="txt">Lorem ipsum dolor sit amet, consectetur adipiscing elit, sed do eiusmod tempor incididunt labore.</p></div>
    <div class="abs news" style="left:35px;top:980px"><div class="datebox"><small>OCT</small><strong>18</strong></div><p class="txt">Lorem ipsum dolor sit amet, consectetur adipiscing elit, sed do eiusmod tempor incididunt labore.</p></div>
  </section>

  <footer>
    <div class="abs footer"></div>
    <div class="abs fcol" style="left:35px;width:170px">
      <h4>About us</h4>
      <p>A member-led trade council promoting open technical data, training and fair dialog across the vehicle service and tool making industry.</p>
      <div class="subscribe"><span>Enter your email</span><b>GO</b></div>
    </div>
    <div class="abs fcol" style="left:230px;width:170px">
      <h4>Contact us</h4>
      <div class="contact-row"><svg width="7" height="9" viewBox="0 0 7 9"><path d="M3.5 0A3.5 3.5 0 0 0 0 3.5C0 6 3.5 9 3.5 9S7 6 7 3.5A3.5 3.5 0 0 0 3.5 0z" fill="#fff"/></svg><p>12 Harlow Park Building, Suite 40<br>Westbrook, ST 40120</p></div>
      <div class="contact-row"><svg width="7" height="7" viewBox="0 0 7 7"><path d="M1 0h2l.6 1.8-1 .8a4 4 0 0 0 1.8 1.8l.8-1L7 4v2c0 .6-.4 1-1 1A6 6 0 0 1 0 1c0-.6.4-1 1-1z" fill="#fff"/></svg><p>+1 (555) 014-2280</p></div>
      <div class="contact-row"><svg width="8" height="6" viewBox="0 0 8 6"><rect width="8" height="6" fill="#fff"/><path d="M0 0l4 3.5L8 0" fill="none" stroke="#0a4a8c" stroke-width=".8"/></svg><p>info@vantortoolcouncil.org</p></div>
    </div>
    <div class="abs fcol" style="left:430px;width:120px">
      <h4>Links</h4>
      <ul><li>Home</li><li>About VTC</li><li>News</li><li>Membership</li><li>Events</li><li>Members Only</li><li>Contact Us</li></ul>
    </div>
    <div class="abs fcol" style="left:600px;width:120px">
      <h4>Follow us</h4>
      <ul class="social"><li><i></i>Community</li><li><i></i>Updates</li><li><i></i>Videos</li><li><i></i>Network</li></ul>
    </div>
    <div class="abs copy">© 2015 Vantor Tool Council. All rights reserved.</div>
  </footer>

</div>
</body>
</html>
```